Milo's Sweet Harbor Package Design

A logo has already been made and now i need to incorporate that logo into a package design. Milo's Sweet Harbor products will be sold in retail stores and its package should appeal to both adults and children. Milo's Sweet Harbor sells candy, nuts and other snacks. Files attached will be logo files and pictures of similar package. Please refer to the files for package design. The physical package consists of a printed card (5.75 inches X 4 inches) and a plastic bag. The card is folded over the plastic bag, sealed and hole punched. The design on the card(5.75 inches X 4 inches) should consist of the logo, price(in this case it is $1.99 however it will vary for other products) and product type (in this case its apple(however it will change for other products). On the "back side"(the card is folded down the middle over the plastic and the top of the card becomes the back side, notice how in the example the top half is upside down, this is correct) should include nutrition facts, ingredients, a UPC barcode and the company information(again these vary depending on the product except for the company information that will be same for all products. Company info - "Packaged & Distributed By: Brightfield Treat Supply
7312 Orchardvale Rd Suite 208 Sterling Heights, Michigan 48297 586-555-0173"

TO WHOEVER WINS THE CONTEST WE WILL COMMISSION YOU TO USE THE SAME DESIGN AND ADD THE NECESSARY INFORMATION(upc, ingredients list, nutritional facts, etc) FOR THE MULTIPLE FLAVORS THAT WE WILL BE PRODUCING UNDER THE Milo's Sweet Harbor BRAND.

```html
<!DOCTYPE html>
<html lang="en">
<head>
<meta charset="utf-8">
<title>Milo's Sweet Harbor – Package Card</title>
<link href="https://fonts.googleapis.com/css2?family=Arimo:wght@400;700&family=Libre+Baskerville:wght@700&display=swap" rel="stylesheet">
<style>
  :root{
    --stage:#58585a;
    --card-pink:#f7b9d0;
    --card-light:#fbd6e4;
    --band-deep:#e8365f;
    --band-mid:#f25a7d;
    --band-light:#ff93ad;
    --fold:#d92a53;
    --ink:#111;
    --text-rose:#c8436a;
    --logo-ring:#c23a62;
    --logo-fill:#f4e2ea;
    --badge-ring:#e56e93;
    --price:#d92a53;
    --white:#fff;
  }
  *{box-sizing:border-box;margin:0;padding:0}
  html,body{width:1200px;height:892px;overflow:hidden}
  body{background:var(--stage);position:relative;font-family:"Arimo",Arial,sans-serif}
  .card{
    position:absolute;left:92px;top:94px;width:1016px;height:706px;overflow:hidden;
    background:radial-gradient(circle at 50% 50%,var(--card-light) 0%,var(--card-pink) 75%);
    box-shadow:6px 8px 14px rgba(0,0,0,.35);
  }
  .card__art{position:absolute;inset:0}
  .back-panel{position:absolute;left:0;top:0;width:1016px;height:353px}
  .nutrition{
    position:absolute;left:46px;top:16px;width:222px;height:320px;background:var(--white);
    transform:rotate(180deg);padding:6px 8px;color:var(--ink);font-size:9px;line-height:1.2;
  }
  .nutrition__box{border:1px solid var(--ink);height:100%;padding:4px 5px}
  .nutrition__title{font-size:23px;font-weight:700;letter-spacing:1px;line-height:1}
  .nutrition__servings{font-size:10px;margin-top:3px}
  .nutrition__size{display:flex;justify-content:space-between;font-size:11px;font-weight:700;border-bottom:6px solid var(--ink);padding-bottom:2px}
  .nutrition__amount{font-size:8px;font-weight:700;margin-top:2px}
  .nutrition__calories{display:flex;justify-content:space-between;align-items:flex-end;font-weight:700;border-bottom:4px solid var(--ink);line-height:1}
  .nutrition__calories span:first-child{font-size:17px}
  .nutrition__calories span:last-child{font-size:25px}
  .nutrition__dv{font-size:6px;font-weight:700;text-align:right;border-bottom:1px solid var(--ink);padding:2px 0}
  .nutrition__row{display:flex;justify-content:space-between;border-bottom:1px solid var(--ink);padding:2px 0;font-size:8.5px}
  .nutrition__row--indent{padding-left:10px}
  .nutrition__row--indent2{padding-left:20px}
  .nutrition__row--last{border-bottom:6px solid var(--ink)}
  .nutrition__note{font-size:6px;margin-top:3px;line-height:1.25}
  .code-area{position:absolute;left:361px;top:36px;width:285px;height:131px;background:var(--white)}
  .ingredients{
    position:absolute;left:708px;top:26px;width:268px;height:184px;transform:rotate(180deg);
    color:var(--text-rose);font-size:17.5px;line-height:22px;
  }
  .brand{position:absolute;left:100px;top:426px;width:240px;height:240px;border-radius:50%;background:var(--logo-fill);border:8px solid var(--logo-ring);display:flex;align-items:center;justify-content:center;text-align:center}
  .brand__name{font-size:30px;font-weight:700;color:var(--logo-ring);line-height:1.15}
  .candy-art{position:absolute;left:612px;top:382px;width:344px;height:324px;border-radius:40% 45% 10% 20%;
    background:radial-gradient(circle at 45% 50%,#f6a53a 0%,#ef5e7c 40%,#d64a8a 70%,rgba(247,185,208,0) 100%)}
  .price-badge{position:absolute;left:720px;top:484px;width:124px;height:124px;border-radius:50%;background:var(--white);border:5px solid var(--badge-ring);display:flex;align-items:center;justify-content:center}
  .price-badge__value{font-family:"Libre Baskerville",Georgia,serif;font-weight:700;font-size:28px;color:var(--price);transform:rotate(-8deg)}
</style>
</head>
<body>
<main class="card">
  <svg class="card__art" width="1016" height="706" viewBox="0 0 1016 706" aria-hidden="true">
    <defs>
      <linearGradient id="bandGrad" x1="0" y1="0" x2="0" y2="1">
        <stop offset="0" stop-color="var(--band-light)"/>
        <stop offset=".35" stop-color="var(--band-mid)"/>
        <stop offset="1" stop-color="var(--band-deep)"/>
      </linearGradient>
    </defs>
    <path id="dripTop" fill="url(#bandGrad)" d="M0,268 C40,262 70,275 110,282 C150,289 170,262 210,262 C260,262 280,292 330,290 C370,288 385,250 420,238 C455,226 470,262 510,270 C560,280 580,236 630,240 C680,244 690,290 740,288 C790,286 800,248 840,250 C880,252 900,282 940,280 C975,278 995,262 1016,266 L1016,353 L0,353 Z"/>
    <use href="#dripTop" transform="translate(0,706) scale(1,-1)"/>
    <line x1="0" y1="353" x2="1016" y2="353" stroke="var(--fold)" stroke-width="2"/>
    <path class="hang-hole" fill="#fff" stroke="#333" stroke-width="1.5" d="M440,273 L575,273 A18,18 0 0 1 575,310 L531,310 C526,330 489,330 484,310 L440,310 A18,18 0 0 1 440,273 Z"/>
    <path class="hang-hole" fill="#fff" stroke="#333" stroke-width="1.5" d="M440,433 L575,433 A18,18 0 0 0 575,396 L531,396 C526,376 489,376 484,396 L440,396 A18,18 0 0 0 440,433 Z"/>
  </svg>

  <section class="back-panel">
    <div class="nutrition">
      <div class="nutrition__box">
        <div class="nutrition__title">Nutrition Facts</div>
        <div class="nutrition__servings">6 servings per container</div>
        <div class="nutrition__size"><span>Serving size</span><span>10 pcs (10g)</span></div>
        <div class="nutrition__amount">Amount Per Serving</div>
        <div class="nutrition__calories"><span>Calories</span><span>110</span></div>
        <div class="nutrition__dv">% Daily Value*</div>
        <div class="nutrition__row"><span><b>Total Fat</b> 2.5g</span><span>3%</span></div>
        <div class="nutrition__row nutrition__row--indent"><span>Saturated Fat 1g</span><span>5%</span></div>
        <div class="nutrition__row nutrition__row--indent"><span><i>Trans</i> Fat 0g</span><span></span></div>
        <div class="nutrition__row"><span><b>Sodium</b> 10mg</span><span>0%</span></div>
        <div class="nutrition__row"><span><b>Total Carbohydrate</b> 22g</span><span>8%</span></div>
        <div class="nutrition__row nutrition__row--indent"><span>Dietary Fiber 0g</span><span>0%</span></div>
        <div class="nutrition__row nutrition__row--indent"><span>Total Sugars 16g</span><span></span></div>
        <div class="nutrition__row nutrition__row--indent2"><span>Includes 0g Added Sugars</span><span>0%</span></div>
        <div class="nutrition__row nutrition__row--last"><span><b>Protein</b> 0g</span><span>0%</span></div>
        <div class="nutrition__note">Not a significant source of cholesterol, vitamin D, calcium, iron, and potassium</div>
        <div class="nutrition__note">* The % Daily Value (DV) tells you how much a nutrient in a serving of food contributes to a daily diet. 2,000 calories a day is used for general nutrition advice.</div>
      </div>
    </div>
    <div class="code-area"></div>
    <p class="ingredients">Ingredients: Lorem dolor amet, consectetuer adipiscing elit, sed diam nonummy nibh euismod tincidunt ut laoreet aliquam . Ut wisi enim ad minim veniam, &nbsp;Lorem ipsum dolor sit amet, consectetuer adipiscing elit,magna aliquam volutpat. Ut wisi enim ad veniam.</p>
  </section>

  <section class="front-panel">
    <div class="brand"><span class="brand__name">Milo's<br>Sweet Harbor</span></div>
    <div class="candy-art" role="img" aria-label="Illustration of colourful lollipops, candy canes and sweets"></div>
    <div class="price-badge"><span class="price-badge__value">$1.99</span></div>
  </section>
</main>
</body>
</html>
```